Brenwick Structures Construction Company Seeking Modern Website

We are a small construction company wanting to create a web presence. We don't have much in the way of current content but will get photos as they come in. Attached is a picture of our business card.
The pages we would like on the menu are:
Home
Portfolio
Product Specs
Testimonials
Our Process
Contact
Some designs we like are:
http://www.tovasheds-example.com/
http://www.qrnstructures-example.com/
http://dunholtbarns-example.com/
http://pellingframes-example.com/
Not much requirements other than that so feel free to be creative!
Updates
Target Market(s)
Construction
Commercial and Residential Buildings
Industry/Entity Type
Construction Company
Number of Pages Required
5+ page
Look and feel

```html
<!DOCTYPE html>
<html lang="en">
<head>
<meta charset="utf-8">
<title>Brenwick Structures</title>
<link rel="stylesheet" href="https://fonts.googleapis.com/css2?family=Ubuntu:wght@300;400;500;700&family=Raleway:wght@300;400&display=swap">
<style>
:root{
  --red:#d32f26;
  --blue:#1a9fd8;
  --blue-dark:#0d86c4;
  --nav:#262626;
  --ink:#333;
  --muted:#888;
  --light:#f1f1f1;
  --white:#fff;
}
*{margin:0;padding:0;box-sizing:border-box}
html,body{width:852px;height:1200px;overflow:hidden;background:var(--white)}
body{position:relative;font-family:'Ubuntu',sans-serif;color:var(--ink)}
.abs{position:absolute}
.top-line{left:0;top:0;width:852px;height:2px;background:var(--blue)}
.brand{font-family:'Ubuntu',sans-serif;font-weight:700;font-size:21px;color:var(--blue-dark);letter-spacing:-.3px}
.header-brand{left:70px;top:28px}
.info{font-size:9px;line-height:16px}
.info strong{display:block;font-weight:500;color:var(--ink)}
.info span{color:var(--muted)}
.info-hours{left:542px;top:26px}
.info-place{left:673px;top:26px}
.icon{position:absolute}
.nav{left:70px;top:81px;width:712px;height:41px;background:var(--nav);box-shadow:0 2px 4px rgba(0,0,0,.3);z-index:2}
.nav a{position:absolute;top:0;height:41px;line-height:41px;font-size:8.5px;color:var(--white);text-decoration:none;letter-spacing:.3px}
.nav a.active{left:0;width:72px;background:var(--red);text-align:center}
.nav .divider{position:absolute;left:596px;top:8px;width:1px;height:25px;background:#555}
.nav .phone{position:absolute;left:631px;top:8px;color:var(--white);font-size:10px;font-weight:500;line-height:13px}
.nav .phone small{display:block;font-size:8px;font-weight:400;color:#ccc}
.hero{left:0;top:101px;width:852px;height:373px;background:linear-gradient(180deg,#6f8db3 0%,#9bb0c8 22%,#6b5546 45%,#7a4a38 70%,#4f5c3a 100%)}
.hero h1{position:absolute;left:0;top:150px;width:852px;text-align:center;font-family:'Raleway',sans-serif;font-weight:300;font-size:50px;color:var(--white);letter-spacing:.5px}
.welcome{left:0;top:474px;width:852px;height:179px;background:linear-gradient(180deg,#29b3e6,#0f89c6);text-align:center;color:var(--white)}
.welcome h2{margin-top:20px;font-weight:400;font-size:17.5px}
.welcome .lead{margin-top:4px;font-size:11.5px}
.welcome p.body{margin:10px auto 0;width:700px;font-size:7.3px;line-height:14.4px;font-weight:300}
.btn{display:inline-block;margin-top:16px;width:100px;height:28px;line-height:26px;border:1px solid var(--white);font-size:11.5px;color:var(--white);text-decoration:none}
.section-title{left:0;width:852px;text-align:center;font-weight:400}
.targets-title{top:675px;font-size:17px;color:#444}
.card{top:722px;width:347px;height:156px}
.card .photo{width:347px;height:122px}
.card .bar{height:34px;padding-left:12px;line-height:34px;color:var(--white);font-size:12.5px;position:relative}
.card .bar svg{position:absolute;right:11px;top:11px}
.card-commercial{left:70px}
.card-commercial .photo{background:linear-gradient(180deg,#3b6fd0,#8eaee0 60%,#d8dde6)}
.card-commercial .bar{background:var(--red)}
.card-residential{left:434px}
.card-residential .photo{background:linear-gradient(180deg,#a7b9c9,#7d7a6c 55%,#6a5642)}
.card-residential .bar{background:var(--blue)}
.galleries{left:0;top:904px;width:852px;height:188px;background:var(--light)}
.galleries-title{top:920px;font-size:17px;color:var(--red)}
.thumb{top:964px;width:160px;height:100px}
.g1{left:70px;background:linear-gradient(135deg,#e9eef3,#bcc8d4)}
.g2{left:254px;background:linear-gradient(180deg,#b9c7d4,#7f6a52)}
.g3{left:438px;background:linear-gradient(180deg,#5c7eb0,#8a8f96 55%,#4f7c3c)}
.g4{left:622px;background:linear-gradient(135deg,#efe3dc,#c9a08e)}
.footer{left:0;top:1092px;width:852px;height:108px;background:var(--red);border-top:3px solid #222}
.footer .brand{position:absolute;left:70px;top:18px;color:var(--white)}
.footer-links{position:absolute;right:70px;top:19px;font-size:8.5px;color:var(--white)}
.footer-links a{color:var(--white);text-decoration:none}
.footer-links i{font-style:normal;margin:0 8px}
.copy{position:absolute;left:70px;top:63px;font-size:8.5px;color:var(--white)}
.social{position:absolute;left:608px;top:60px;font-size:8px;color:var(--white)}
.social-dots{position:absolute;left:682px;top:54px}
</style>
</head>
<body>
<div class="abs top-line"></div>

<div class="abs brand header-brand">Brenwick Structures</div>

<svg class="icon" style="left:522px;top:29px" width="12" height="12" viewBox="0 0 12 12" aria-hidden="true"><circle cx="6" cy="6" r="4.8" fill="none" stroke="#d32f26" stroke-width="1.4"/><path d="M6 3.5V6H8" fill="none" stroke="#d32f26" stroke-width="1.2"/></svg>
<div class="abs info info-hours"><strong>Mon - Sat 8.00 - 18.00</strong><span>Sunday Closed</span></div>

<svg class="icon" style="left:657px;top:29px" width="10" height="14" viewBox="0 0 10 14" aria-hidden="true"><path d="M5 13C5 13 1 8 1 5a4 4 0 0 1 8 0c0 3-4 8-4 8z" fill="#1a9fd8"/><circle cx="5" cy="5" r="1.5" fill="#fff"/></svg>
<div class="abs info info-place"><strong>At vero eos et accusamus</strong><span>Et iusto odio dignissimos</span></div>

<nav class="abs nav">
  <a class="active" href="#">HOME</a>
  <a style="left:96px" href="#">PORTFOLIO</a>
  <a style="left:190px" href="#">PRODUCT SPECS</a>
  <a style="left:303px" href="#">TESTIMONIALS</a>
  <a style="left:409px" href="#">OUR PROCESS</a>
  <a style="left:512px" href="#">CONTACT</a>
  <span class="divider"></span>
  <svg class="icon" style="left:614px;top:11px" width="12" height="12" viewBox="0 0 12 12" aria-hidden="true"><path d="M2.5 1l2 2.2-1 1.3c.8 1.6 1.9 2.7 3.5 3.5l1.3-1L10.5 9l-1 1.8C5.5 10.5 1.5 6.5 1 2.2z" fill="#e0553b"/></svg>
  <div class="phone">555 014 2297<small>Free call</small></div>
</nav>

<section class="abs hero" role="img" aria-label="Photo of a brick family house with a gabled shingle roof and garage">
  <svg class="icon" style="left:21px;top:142px" width="14" height="30" viewBox="0 0 14 30" aria-hidden="true"><path d="M13 1L1 15l12 14" fill="none" stroke="#fff" stroke-width="1.5"/></svg>
  <svg class="icon" style="left:816px;top:142px" width="14" height="30" viewBox="0 0 14 30" aria-hidden="true"><path d="M1 1l12 14L1 29" fill="none" stroke="#fff" stroke-width="1.5"/></svg>
  <h1>Nam libero tempore</h1>
</section>

<section class="abs welcome">
  <h2>WELCOME TO BRENWICK STRUCTURES</h2>
  <div class="lead">On the other hand, we denounce</div>
  <p class="body">Sed ut perspiciatis unde omnis iste natus error sit voluptatem accusantium doloremque laudantium, totam rem aperiam, eaque ipsa quae ab illo inventore veritatis et quasi architecto beatae vitae dicta sunt explicabo. Nemo enim ipsam voluptatem quia voluptas sit aspernatur aut odit aut fugit, sed quia consequuntur magni dolores eos qui ratione voluptatem sequi nesciunt.vel illum qui dolorem eum fugiat quo voluptas nulla pariatur</p>
  <a class="btn" href="#">READ MORE</a>
</section>

<h3 class="abs section-title targets-title">OUR TARGETS</h3>

<div class="abs card card-commercial">
  <div class="photo" role="img" aria-label="Photo of tall white apartment towers against a blue sky"></div>
  <div class="bar">COMMERCIAL CONSTRUCTION
    <svg width="12" height="12" viewBox="0 0 12 12" aria-hidden="true"><circle cx="6" cy="6" r="5" fill="none" stroke="#fff" stroke-width="1.3"/><path d="M3.5 6h4M6 4l2 2-2 2" fill="none" stroke="#fff" stroke-width="1.3"/></svg>
  </div>
</div>

<div class="abs card card-residential">
  <div class="photo" role="img" aria-label="Photo of a site worker at a building frame under construction"></div>
  <div class="bar">RESIDENTIAL BUILDINGS
    <svg width="12" height="12" viewBox="0 0 12 12" aria-hidden="true"><circle cx="6" cy="6" r="5" fill="none" stroke="#fff" stroke-width="1.3"/><path d="M3.5 6h4M6 4l2 2-2 2" fill="none" stroke="#fff" stroke-width="1.3"/></svg>
  </div>
</div>

<section class="abs galleries"></section>
<h3 class="abs section-title galleries-title">OUR GALLERIES</h3>
<div class="abs thumb g1" role="img" aria-label="Photo of blueprints, glasses and a hard hat on a desk"></div>
<div class="abs thumb g2" role="img" aria-label="Photo of a crane and concrete columns on a building site"></div>
<div class="abs thumb g3" role="img" aria-label="Photo of a two-storey suburban house at dusk"></div>
<div class="abs thumb g4" role="img" aria-label="Photo of hands sheltering a small model house"></div>

<footer class="abs footer">
  <div class="brand">Brenwick Structures</div>
  <div class="footer-links"><a href="#">Home</a><i>/</i><a href="#">Portfolio</a><i>/</i><a href="#">Product Specs</a><i>/</i><a href="#">Testimonials</a><i>/</i><a href="#">Our Process</a><i>/</i><a href="#">Contact</a></div>
  <div class="copy">Copyright © 2015 Brenwick Structures &nbsp;|&nbsp; All Rights Reserved</div>
  <div class="social">Stay Connected:</div>
  <svg class="social-dots" width="100" height="22" viewBox="0 0 100 22" aria-label="Social links">
    <circle cx="11" cy="11" r="10" fill="#e0463c"/>
    <circle cx="36" cy="11" r="10" fill="#e0463c"/>
    <circle cx="62" cy="11" r="10" fill="#e0463c"/>
    <circle cx="88" cy="11" r="10" fill="#e0463c"/>
  </svg>
</footer>
</body>
</html>
```